Communication and Marketing agency needs a new presentation card

We are a group of communication and marketing agencies specialized in companies that are in the logistics and industrial sector. The head agency is TELVANO Grupo and the group consists of 4 agencies: TELVANO Media, TELVANO Digital, TELVANO Research and DifundeEnPantalla. We hace 4 offices in Spain (Madrid, Barcelona, Valencia and Murcia). We are looking for a clean and attractive design that transmits our experience, brand presence in the market and knowledge to those who receive the card.It has to maintain the colors of the logo that is attached.
Target Market(s)
logistics and industrial sector
Marketing department
Contact Information for Business Card
Clean and attractive design

```html
<!DOCTYPE html>
<html lang="en">
<head>
<meta charset="UTF-8">
<title>TELVANO Grupo – Business Card</title>
<link href="https://fonts.googleapis.com/css2?family=Bebas+Neue&family=PT+Sans:wght@400&family=Lato:wght@400;700&display=swap" rel="stylesheet">
<style>
  :root {
    --brand-red: #ad1e28;
    --backdrop-red: #b0232f;
    --card-white: #ffffff;
    --ink-dark: #2e2e2e;
    --ink-grey: #4a4a4a;
  }
  * { margin: 0; padding: 0; box-sizing: border-box; }
  html, body { width: 1200px; height: 1200px; overflow: hidden; }
  body { background: var(--backdrop-red); position: relative; font-family: "PT Sans", sans-serif; }

  .card {
    position: absolute;
    left: 224px;
    width: 814px;
    height: 465px;
    border-radius: 32px;
  }
  .card--front { top: 76px; background: var(--card-white); }
  .card--back { top: 658px; background: var(--brand-red); }

  .brand-name {
    position: absolute;
    font-family: "Bebas Neue", sans-serif;
    font-weight: 400;
    text-align: right;
    line-height: 0.9;
    letter-spacing: 6px;
  }
  .brand-name .brand-main { display: block; font-size: 100px; }
  .brand-name .brand-sub { display: block; font-size: 62px; letter-spacing: 2px; }
  .card--front .brand-name { right: 64px; top: 84px; color: var(--brand-red); }
  .card--back .brand-name { right: 200px; top: 150px; color: var(--card-white); }

  .holder-name {
    position: absolute;
    left: 66px;
    top: 266px;
    font-family: "Bebas Neue", sans-serif;
    font-size: 40px;
    line-height: 1;
    color: var(--ink-dark);
    letter-spacing: 0.5px;
  }
  .holder-name .first-name { color: var(--brand-red); }
  .holder-role {
    position: absolute;
    left: 66px;
    top: 302px;
    font-size: 18px;
    color: var(--ink-dark);
  }

  .accent-rule {
    position: absolute;
    top: 337px;
    width: 51px;
    height: 3px;
    background: var(--brand-red);
  }
  .accent-rule--left { left: 66px; }
  .accent-rule--right { left: 553px; }

  .contact-list {
    position: absolute;
    list-style: none;
    font-size: 18px;
    line-height: 23.5px;
    color: var(--ink-dark);
  }
  .contact-list--left { left: 66px; top: 352px; }
  .contact-list--right { left: 553px; top: 349px; }
  .contact-label { color: var(--brand-red); font-weight: 700; }
  .web-highlight { color: var(--brand-red); }

  .office-cities {
    position: absolute;
    left: 0;
    right: 0;
    top: 405px;
    text-align: center;
    font-family: "Lato", sans-serif;
    font-weight: 700;
    font-size: 22px;
    color: var(--card-white);
    letter-spacing: 0.3px;
  }
  .office-cities .marker { font-weight: 400; margin: 0 8px; }
</style>
</head>
<body>
  <section class="card card--front">
    <div class="brand-name">
      <span class="brand-main">TELVANO</span>
      <span class="brand-sub">Grupo</span>
    </div>

    <h1 class="holder-name"><span class="first-name">MARCO</span> ELLISON</h1>
    <p class="holder-role">MANAGER</p>

    <div class="accent-rule accent-rule--left"></div>
    <ul class="contact-list contact-list--left">
      <li><span class="contact-label">P.</span> +(402)&nbsp; -555- 0147</li>
      <li><span class="contact-label">F.</span> +(402)&nbsp; -555- 0147</li>
      <li>info@telvanogroup.com</li>
    </ul>

    <div class="accent-rule accent-rule--right"></div>
    <ul class="contact-list contact-list--right">
      <li>1840 North Elmwood Avenue,</li>
      <li>Lincoln, NE 68521</li>
      <li>www.<span class="web-highlight">telvanoinfo</span>.com</li>
    </ul>
  </section>

  <section class="card card--back">
    <div class="brand-name">
      <span class="brand-main">TELVANO</span>
      <span class="brand-sub">Grupo</span>
    </div>
    <p class="office-cities"><span class="marker">&gt;&gt;</span>Madrid | Barcelona | Valencia | Murcia<span class="marker">&lt;&lt;</span></p>
  </section>
</body>
</html>
```